Retail Jewelry Business Card Design Project

We are in need of a new business card design for a retail jewelry store. This store is in the business of fine jewelry including but not specific to bridal jewelry, diamonds, designer jewelry and watches.

This store has been in business for 20 years but continues to strive for a modern professional appeal. The main colors use for this business are a royal blue, white and silver.

Target Market(s)

Target market is ages 18-50

Industry/Entity Type

Jewelry

Requirements
Must have
• Sales Person Name
Sales Person Email Address

Store Address
Store Phone
Website

Standard business card size. No odd shapes or sizes.
Nice to have
• Overall modern feel for card.

We have thought that a design with a nice feature of the logo on the back of the card would be nice but open to ideas.
Should not have
• No specific images of jewelry should be used.

```html
<!DOCTYPE html>
<html lang="en">
<head>
<meta charset="utf-8">
<title>Marlowe Reed Fine Jewelry – Business Card</title>
<link rel="stylesheet" href="https://fonts.googleapis.com/css2?family=Open+Sans:wght@400;600&display=swap">
<style>
  :root {
    --backdrop: #e9e6e1;
    --navy-deep: #0f2746;
    --navy-mid: #1a3a5e;
    --navy-light: #25496d;
    --band: #102a4b;
    --gold: #d9b24a;
    --white: #ffffff;
    --shadow: rgba(20, 20, 30, 0.35);
  }
  * { margin: 0; padding: 0; box-sizing: border-box; }
  html, body {
    width: 1200px;
    height: 1000px;
    overflow: hidden;
    background: var(--backdrop);
    font-family: "Open Sans", Arial, sans-serif;
  }
  .canvas { position: relative; width: 1200px; height: 1000px; }

  .card {
    position: absolute;
    width: 640px;
    height: 366px;
    overflow: hidden;
    box-shadow: 0 14px 30px var(--shadow);
  }

  /* Front: contact side */
  .card-front {
    left: 70px;
    top: 70px;
    background: linear-gradient(180deg, var(--navy-deep) 0%, var(--navy-light) 82%);
  }
  .card-front .wordmark {
    position: absolute;
    left: 52px;
    top: 150px;
    color: var(--gold);
    font-weight: 600;
    line-height: 1.15;
  }
  .card-front .wordmark .name { font-size: 26px; letter-spacing: 0.5px; }
  .card-front .wordmark .line { font-size: 12px; letter-spacing: 3px; }
  .contact {
    position: absolute;
    left: 330px;
    top: 66px;
    color: var(--white);
    font-size: 14px;
    line-height: 1.35;
  }
  .contact .store { font-size: 16px; margin-bottom: 20px; }
  .contact p { margin-bottom: 18px; }
  .web-band {
    position: absolute;
    left: 0; right: 0; bottom: 0;
    height: 64px;
    background: var(--band);
    color: var(--white);
    font-size: 16px;
    display: flex;
    align-items: center;
    justify-content: center;
    padding-left: 80px;
  }

  /* Back: feature side */
  .card-back {
    left: 490px;
    top: 560px;
    background: linear-gradient(180deg, var(--navy-mid) 0%, var(--navy-deep) 100%);
  }
  .card-back .top-panel {
    position: absolute;
    left: 0; right: 0; top: 0;
    height: 130px;
    background: linear-gradient(180deg, var(--navy-deep) 0%, var(--navy-light) 100%);
  }
  .card-back .wordmark {
    position: absolute;
    left: 0; right: 0;
    top: 120px;
    text-align: center;
    color: var(--gold);
    font-weight: 600;
    line-height: 1.1;
  }
  .card-back .wordmark .name { font-size: 54px; letter-spacing: 1px; }
  .card-back .wordmark .line { font-size: 22px; letter-spacing: 7px; margin-top: 6px; }
</style>
</head>
<body>
<main class="canvas">
  <section class="card card-front" aria-label="Business card front">
    <div class="wordmark">
      <div class="name">Marlowe Reed</div>
      <div class="line">FINE JEWELRY</div>
    </div>
    <div class="contact">
      <p class="store">Marlowe Reed Fine Jewelry</p>
      <p>location: 2280 Linden Avenue<br>Harbor City, FL 32990</p>
      <p>mail: marlowe@marlowereedjewelry.com</p>
      <p>tel: (555) 014 - 2287</p>
    </div>
    <div class="web-band">www.marlowereedjewelry.com</div>
  </section>

  <section class="card card-back" aria-label="Business card back">
    <div class="top-panel"></div>
    <div class="wordmark">
      <div class="name">Marlowe Reed</div>
      <div class="line">FINE JEWELRY</div>
    </div>
  </section>
</main>
</body>
</html>
```